Suchen ansprechendes & seriöses Urkunden/Zertifikat Design für Webseite & Druck
Zielgruppe
Auf unserer Webseite http://wacker-im-alter.de können sich Unternehmen, Institutionen und Vereine ihre Seniorenfreundlichkeit durch ein Zertifikat bestätigen und zertifizieren lassen.
Unsere Kundengruppen: Hotel – Gastronomie – Wellness – Reisen und Touristik – Touristikregionen – Seniorenshop – Onlineshop – Unternehmen als Dienstleister – Medizin und Health-Service – Apotheke – Altenheim – Pflegeheim – Seniorenheim – Vereine – Seniorenservice – Zahnärzte – Fitnessstudio – Sportstudio – Physiotherapie – Sportverein – Golfclub – und viele weitere seniorenfreundliche Institutionen.
Aufgabenstellung
Auftrag- Ausschreibung:
- Erstellung eines Design:
- Urkunde für Webseite wacker-im-alter.de - Das Zertifikat "Wacker im Alter“
Funktion:
Kunde erkennt das Zertifikat - Logo auf einer Webseite und Klickt auf dieses.
Er wird weitergeleitet auf eine Unterseite, worin die Richtlinien und die Urkunde sichtbar wird.
Zielgruppe:
- Unternehmen, welche das Zertifikat auf Ihre Webseite setzen. Die Urkunde gibt Auskunft, dass der Dienstleister einen besonderen Service für Senioren ausübt. Die Urkunde ist sichtbar auf der Webseite, indem das Logo angeklickt wird. Die Urkunde gibt es ebenfalls als Download, damit der Kunde diese in seinen Geschäftsräumen aufhängen kann oder diese in seinen Werbeunterlagen präsentieren kann.
- Verbraucher sollen beeindruckt sein, von der Urkunde, welches Vertrauen ausstrahlt, aber auch Seriosität
Folgende Ausstrahlung soll die Urkunde haben:
- Soll Mitbewerber des Zertifikatsinhaber beeindrucken und das Verlangen aufzeigen, sich ebenfalls zertifizieren zu lassen ( ca: 70% der Kunden sind Mitbewerber … ). Nach dem Motto "Das Logo ist super und edel, das muss ich auch haben!"
- Der Kunde als Verbraucher soll Vertrauen gewinnen, die Daten sollen gut sichtbar sein, aber nicht verkitscht wie eine Urkunde bei einer Kaffeefahrt. Der Verbraucher geht auf das Zertifikat und kommt zur Urkunde, deshalb soll die Farbe, und Darstellung, Seriosität des Unternehmens ausstrahlen.
Sonstiges
- Die Urkunde soll dem neuen Design unserer Seite (zu sehen unter: http://gutsiegel-pruefung.de) angepasst sein.
- Vor Auftragsendvergabe erhalten Sie noch ein telefonisches Briefing über unsere Erfahrungswerte
Link zur bestehenden alten Webseite (Altes Design): http://wacker-im-alter.de
Info Verbraucher: http://www.wacker-im-alter.de/verbraucher/
Info zum Zertifikat: http://www.wacker-im-al..

```html
<!DOCTYPE html>
<html lang="de">
<head>
<meta charset="utf-8">
<title>Zertifikat – Wacker im Alter</title>
<link rel="stylesheet" href="https://fonts.googleapis.com/css2?family=Oswald:wght@300;400;600&family=Open+Sans:wght@400;600;700&display=swap">
<style>
  :root {
    --gold-light: #f4e6c3;
    --gold-mid: #e2c995;
    --gold-deep: #cfae72;
    --frame: #fffaf0;
    --band-red: #b3271f;
    --band-red-dark: #8e1c16;
    --ink: #1f1a14;
    --ink-soft: #3a322a;
    --title-white: #ffffff;
    --seal-face: #e4e4e6;
    --seal-ring: #b9b9bd;
    --sign-tone: #d6bd88;
  }
  * { margin: 0; padding: 0; box-sizing: border-box; }
  html, body { width: 850px; height: 1200px; overflow: hidden; background: #ffffff; }
  .certificate {
    position: relative;
    width: 850px; height: 1200px;
    background: radial-gradient(ellipse at 40% 45%, var(--gold-light) 0%, var(--gold-mid) 60%, var(--gold-deep) 100%);
    font-family: "Open Sans", Arial, sans-serif;
    color: var(--ink);
    overflow: hidden;
  }
  .frame {
    position: absolute; left: 60px; top: 45px; width: 728px; height: 1095px;
    border: 2px solid var(--frame);
  }
  .band { position: absolute; background: var(--band-red); box-shadow: 0 2px 4px rgba(0,0,0,.25); }
  .band--left-wide  { left: 0; top: 98px; width: 166px; height: 66px; }
  .band--left-thin  { left: 0; top: 212px; width: 166px; height: 30px; }
  .band--right-wide { right: 0; top: 98px; width: 170px; height: 66px; }
  .band--right-thin { right: 0; top: 212px; width: 170px; height: 30px; }
  .title {
    position: absolute; left: 0; width: 850px; top: 78px; text-align: center;
    font-family: "Oswald", "Arial Narrow", sans-serif; font-weight: 600;
    font-size: 104px; line-height: 1; letter-spacing: 4px;
    color: var(--title-white); text-shadow: 2px 3px 5px rgba(0,0,0,.35);
  }
  .subtitle {
    position: absolute; left: 0; width: 850px; top: 208px; text-align: center;
    font-family: "Oswald", "Arial Narrow", sans-serif; font-weight: 300;
    font-size: 40px; line-height: 1; letter-spacing: 1px; color: var(--ink-soft);
  }
  .details { position: absolute; left: 0; top: 300px; width: 850px; }
  .row { position: absolute; left: 0; width: 850px; font-size: 27px; line-height: 32px; }
  .row__label {
    position: absolute; right: 520px; text-align: right; font-weight: 700; white-space: nowrap;
  }
  .row__value { position: absolute; left: 342px; font-weight: 400; white-space: nowrap; }
  .seal { position: absolute; left: 515px; top: 770px; width: 240px; height: 240px; }
  .signatures { position: absolute; left: 0; top: 975px; width: 850px; }
  .signature { position: absolute; top: 0; height: 90px; border-radius: 40px; background: radial-gradient(ellipse, var(--sign-tone) 0%, rgba(214,189,136,0) 70%); }
  .signature--first  { left: 320px; width: 150px; }
  .signature--second { left: 540px; width: 150px; }
  .signer { position: absolute; top: 95px; font-size: 20px; color: var(--ink-soft); }
  .signer--first  { left: 360px; }
  .signer--second { left: 565px; }
  .page-number {
    position: absolute; left: 12px; top: 1162px; font-size: 26px; font-weight: 700; color: var(--ink);
  }
</style>
</head>
<body>
<main class="certificate">
  <div class="frame"></div>
  <div class="band band--left-wide"></div>
  <div class="band band--left-thin"></div>
  <div class="band band--right-wide"></div>
  <div class="band band--right-thin"></div>

  <h1 class="title">ZERTIFIKAT</h1>
  <p class="subtitle">WACKER IM ALTER</p>

  <section class="details">
    <div class="row" style="top:0"><span class="row__label">Zertifikat ID:</span><span class="row__value">7250441e9e</span></div>
    <div class="row" style="top:63px"><span class="row__label">Anbieter:</span><span class="row__value">Wacker im Alter<br>Ihr Zertifizierungsdienst</span></div>
    <div class="row" style="top:160px"><span class="row__label">Status:</span><span class="row__value">aktiv</span></div>
    <div class="row" style="top:225px"><span class="row__label">Unternehmen:</span><span class="row__value">Senioren Service Lindner<br>Birkenweg 8<br>54321 Auental<br>Deutschland<br>info@lindner-service.org</span></div>
    <div class="row" style="top:420px"><span class="row__label">Vertretungs-<br>berechtigter:</span><span class="row__value">Frau Helga Lindner</span></div>
    <div class="row" style="top:547px"><span class="row__label">Erstprüfung am:</span><span class="row__value">07.04.2017</span></div>
    <div class="row" style="top:604px"><span class="row__label">gültig bis:</span><span class="row__value">07.04.2019</span></div>
    <div class="row" style="top:756px"><span class="row__label">Bestätigt von:</span></div>
  </section>

  <svg class="seal" viewBox="0 0 240 240" role="img" aria-label="Prüfsiegel">
    <circle cx="120" cy="120" r="112" fill="var(--seal-ring)"/>
    <circle cx="120" cy="120" r="90" fill="var(--seal-face)"/>
  </svg>

  <div class="signatures">
    <div class="signature signature--first" role="img" aria-label="Unterschrift K. Brandt"></div>
    <div class="signature signature--second" role="img" aria-label="Unterschrift M. Ostwald"></div>
    <span class="signer signer--first">K. Brandt</span>
    <span class="signer signer--second">M. Ostwald</span>
  </div>

  <span class="page-number">14</span>
</main>
</body>
</html>
```